Business Card Design

I need business cards designed for a new company i have started that makes cakes, particularly themed kids cakes with a really modern design and I would like to have my business cards reflect this. I have attached some photos of cakes I have made and would like some to be used.

Industry/Entity Type

Business

Contact Information for Business Card

Business Name: Tarts and Treats by Maren
Mobile: 0492 815 063
email: maren@tartsandtreatsbymaren.example.au
Instagram: instagram.com/tartsandtreatsbymaren/
Facebook: fb.me/tartsandtreatsbymaren

Colors
e667a6
b768aa
3276b5

Requirements
Must have
• Business Name: Tarts and Treats by Maren
• Mobile: 0492 815 063
• email: maren@tartsandtreatsbymaren.example.au
• Instagram: instagram.com/tartsandtreatsbymaren/
• Facebook: fb.me/tartsandtreatsbymaren
Nice to have
• 2 to 3 pictures of my cakes

```html
<!DOCTYPE html>
<html lang="en">
<head>
<meta charset="utf-8">
<title>Tarts and Treats by Maren – Business Cards</title>
<link rel="stylesheet" href="https://fonts.googleapis.com/css2?family=Open+Sans:wght@400;600;700&display=swap">
<style>
  :root {
    --pink: #e667a6;
    --pink-deep: #d9549a;
    --pink-soft: #ee8fbf;
    --purple: #b768aa;
    --white: #ffffff;
    --backdrop: #ece8e4;
    --ink-light: #fdf2f8;
  }
  * { margin: 0; padding: 0; box-sizing: border-box; }
  html, body {
    width: 1200px; height: 843px; overflow: hidden;
    background: var(--backdrop);
    font-family: "Open Sans", Arial, sans-serif;
  }
  .canvas {
    position: relative; width: 1200px; height: 843px;
    display: flex; align-items: center; justify-content: center; gap: 40px;
  }
  .card {
    position: relative; width: 540px; height: 309px; overflow: hidden;
    border-radius: 3px;
    box-shadow: 0 6px 18px rgba(0,0,0,0.18);
  }

  /* Back of card */
  .card--back {
    background: linear-gradient(120deg, var(--pink-deep) 0%, var(--pink) 45%, var(--pink-soft) 60%, var(--pink) 100%);
    display: flex; align-items: center; justify-content: center;
  }
  .brand-name {
    font-family: "Open Sans", Arial, sans-serif;
    font-weight: 600; line-height: 1.1; text-align: center;
    display: flex; align-items: center; gap: 12px;
  }
  .brand-name__mark {
    width: 14px; height: 14px; border-radius: 50%; flex: none;
  }
  .card--back .brand-name { color: var(--white); font-size: 30px; }
  .card--back .brand-name__mark { background: var(--white); }

  /* Front of card */
  .card--front { background: var(--white); }
  .card--front .brand-name {
    position: absolute; left: 52px; top: 38px;
    color: var(--pink); font-size: 26px; text-align: left;
  }
  .card--front .brand-name__mark { background: var(--pink); }
  .front-wave { position: absolute; inset: 0; width: 100%; height: 100%; }

  .person {
    position: absolute; left: 22px; top: 190px; color: var(--white);
  }
  .person__name { font-size: 15px; font-weight: 700; letter-spacing: 0.5px; }
  .person__role { font-size: 11.5px; font-weight: 400; margin-top: 1px; }

  .contact-list {
    position: absolute; right: 14px; top: 206px;
    list-style: none; color: var(--ink-light);
    font-size: 11px; line-height: 18.5px;
    display: grid; grid-template-columns: auto 12px;
    column-gap: 8px; align-items: center;
  }
  .contact-list li { display: contents; }
  .contact-list .contact-text { white-space: nowrap; text-align: right; }
  .contact-list .icon { width: 11px; height: 11px; display: block; justify-self: center; }
  .contact-list .icon--none { width: 11px; height: 11px; }
  .contact-list .social-mark {
    width: 10px; height: 10px; background: var(--ink-light); border-radius: 2px;
    display: block; justify-self: center;
  }
</style>
</head>
<body>
<main class="canvas">

  <section class="card card--back" aria-label="Card back">
    <div class="brand-name">
      <span class="brand-name__mark"></span>
      <span>Tarts and Treats<br>by Maren</span>
    </div>
  </section>

  <section class="card card--front" aria-label="Card front">
    <svg class="front-wave" viewBox="0 0 540 309" preserveAspectRatio="none" aria-hidden="true">
      <defs>
        <linearGradient id="frontPink" x1="0" y1="0" x2="1" y2="0.3">
          <stop offset="0" stop-color="#d9549a"/>
          <stop offset="0.45" stop-color="#e667a6"/>
          <stop offset="0.6" stop-color="#ee8fbf"/>
          <stop offset="1" stop-color="#cf5a9c"/>
        </linearGradient>
      </defs>
      <path d="M0,140 C110,128 240,160 360,170 C440,176 505,176 540,186 L540,309 L0,309 Z" fill="#b768aa"/>
      <path d="M0,148 C110,138 240,170 360,180 C440,186 505,186 540,195 L540,309 L0,309 Z" fill="url(#frontPink)"/>
    </svg>

    <div class="brand-name">
      <span class="brand-name__mark"></span>
      <span>Tarts and Treats<br>by Maren</span>
    </div>

    <div class="person">
      <p class="person__name">MAREN ELLIS</p>
      <p class="person__role">CEO/Founder</p>
    </div>

    <ul class="contact-list">
      <li><span class="contact-text">maren@tartsandtreatsbymaren.example.au</span><span class="icon--none"></span></li>
      <li><span class="contact-text">0492 815 063</span>
        <svg class="icon" viewBox="0 0 12 12" aria-hidden="true"><rect x="3" y="0.5" width="6" height="11" rx="1" fill="none" stroke="#fdf2f8" stroke-width="1"/><circle cx="6" cy="9.8" r="0.6" fill="#fdf2f8"/></svg>
      </li>
      <li><span class="contact-text">tartsandtreatsbymaren.example.au</span>
        <svg class="icon" viewBox="0 0 12 12" aria-hidden="true"><rect x="0.5" y="2.5" width="11" height="7" fill="none" stroke="#fdf2f8" stroke-width="1"/><path d="M0.5,2.5 L6,7 L11.5,2.5" fill="none" stroke="#fdf2f8" stroke-width="1"/></svg>
      </li>
      <li><span class="contact-text">tartsandtreatsbymaren</span><span class="social-mark" aria-hidden="true"></span></li>
      <li><span class="contact-text">tartsandtreatsbymaren</span><span class="social-mark" aria-hidden="true"></span></li>
    </ul>
  </section>

</main>
</body>
</html>
```